Label design for our new range of organic honey.

We need a design for honey jars and tubs. The label needs to indicate we are located in the Western Australia. The design needs to be elegant, modern and attracting high end customers that focus on quality.

Need extra days to review

```html
<!DOCTYPE html>
<html lang="en">
<head>
<meta charset="utf-8">
<title>Organic Honey Label</title>
<link rel="stylesheet" href="https://fonts.googleapis.com/css2?family=Source+Serif+4:ital,opsz,wght@0,8..60,400;0,8..60,500;1,8..60,400&display=swap">
<style>
  :root {
    --backdrop: #eaeaea;
    --label-dark: #3b3b3c;
    --label-mid: #4a4a4b;
    --map-tone: #5a5a5c;
    --ink-white: #ffffff;
    --gold-deep: #8a7440;
    --gold-bright: #e9dca8;
    --gold-mid: #b9a265;
  }
  html, body {
    margin: 0;
    padding: 0;
    width: 1200px;
    height: 1200px;
    overflow: hidden;
    background: var(--backdrop);
  }
  .canvas {
    position: relative;
    width: 1200px;
    height: 1200px;
    font-family: "Source Serif 4", Georgia, serif;
  }
  .label-shape {
    position: absolute;
    inset: 0;
  }
  .text-block {
    position: absolute;
    left: 0;
    width: 1200px;
    margin: 0;
    color: var(--ink-white);
    line-height: 1;
  }
  .product-kind {
    top: 508px;
    left: 560px;
    width: 400px;
    text-align: center;
    font-size: 52px;
    font-weight: 500;
  }
  .product-name {
    top: 568px;
    left: 500px;
    width: 480px;
    text-align: center;
    font-size: 116px;
    font-weight: 400;
    letter-spacing: 1px;
    background: linear-gradient(90deg, var(--gold-deep) 0%, var(--gold-bright) 35%, var(--gold-mid) 60%, var(--gold-bright) 85%, var(--gold-deep) 100%);
    -webkit-background-clip: text;
    background-clip: text;
    color: transparent;
  }
  .purity {
    top: 694px;
    left: 560px;
    width: 400px;
    text-align: center;
    font-size: 36px;
    font-weight: 500;
  }
  .brand {
    position: absolute;
    top: 560px;
    left: 248px;
    width: 200px;
    display: flex;
    flex-direction: column;
    align-items: center;
    gap: 14px;
  }
  .brand-dot {
    width: 22px;
    height: 22px;
    border-radius: 50%;
    background: var(--gold-mid);
  }
  .brand-name {
    margin: 0;
    color: var(--ink-white);
    font-size: 22px;
    font-weight: 400;
    letter-spacing: 3px;
    text-transform: uppercase;
    text-align: center;
    line-height: 1.35;
  }
  .origin {
    position: absolute;
    top: 822px;
    left: 400px;
    width: 360px;
    margin: 0;
    color: var(--ink-white);
    font-style: italic;
    font-size: 31px;
    line-height: 1.2;
  }
  .origin-from {
    display: block;
    padding-left: 102px;
  }
  .origin-place {
    display: block;
    padding-left: 30px;
  }
  .gold-rule {
    position: absolute;
    top: 914px;
    left: 420px;
    width: 307px;
    height: 12px;
    background: linear-gradient(90deg, var(--gold-deep), var(--gold-bright) 55%, var(--gold-mid));
  }
</style>
</head>
<body>
<main class="canvas">
  <svg class="label-shape" width="1200" height="1200" viewBox="0 0 1200 1200">
    <defs>
      <clipPath id="hexClip">
        <polygon points="150,600 327,185 873,185 1050,600 873,1015 327,1015" stroke-linejoin="round"/>
      </clipPath>
      <linearGradient id="mapTone" x1="0" y1="0" x2="1" y2="1">
        <stop offset="0" stop-color="#616163"/>
        <stop offset="1" stop-color="#4b4b4d"/>
      </linearGradient>
    </defs>
    <polygon class="label-hexagon" points="150,600 327,185 873,185 1050,600 873,1015 327,1015"
      fill="var(--label-dark)" stroke="var(--label-dark)" stroke-width="44" stroke-linejoin="round"/>
    <g clip-path="url(#hexClip)">
      <rect class="map-area" role="img" aria-label="Outline map of Australia"
        x="211" y="256" width="839" height="668" rx="120" fill="url(#mapTone)" opacity="0.45"/>
    </g>
  </svg>

  <div class="brand">
    <span class="brand-dot"></span>
    <p class="brand-name">Redgum Ridge<br>Honey</p>
  </div>

  <p class="text-block product-kind">organic</p>
  <h1 class="text-block product-name">HONEY</h1>
  <p class="text-block purity">100% Pure</p>

  <p class="origin">
    <span class="origin-from">from</span>
    <span class="origin-place">Western Australia</span>
  </p>
  <div class="gold-rule"></div>
</main>
</body>
</html>
```